Harwick State College Sales Presentation to demonstrate instructional design process

We would like the Powerpoint to be re-designed. The content on the screen and in the notes sections must remain the same but it can all be re-styled to look more modern and professional. Please use our logo colors and the final design should communicate professionalism and experience. We typically use the blue and white colors predominately and use the red in the logo sparingly for emphasis.

Target Market(s)

Audience of college educators, sales people, instructional designers, and leaders

Industry/Entity Type

Higher Education and Professional Services

Font styles to use
Sans Serif

Colors
0054AA
0677BA
7BADD7
CADEEF
E8F1F8
EB3D1F
EC4F4E
F09395
F8D3D4
FCEDEE

Requirements
Must have
• clear visuals, same verbiage we have supplied, colorful and artful design
Nice to have
• some animations between slides would be nice.
Should not have
• It should not use red text on black backgrounds.

```html
<!DOCTYPE html>
<html lang="en">
<head>
<meta charset="utf-8">
<title>Harwick State College – Instructional Design Proposal</title>
<link href="https://fonts.googleapis.com/css2?family=Lato:wght@400;700;900&display=swap" rel="stylesheet">
<style>
  :root{
    --navy:#0054AA;
    --blue:#0677BA;
    --bright:#1273DE;
    --sky:#7BADD7;
    --ice:#CADEEF;
    --mist:#E8F1F8;
    --red:#EB3D1F;
    --rose:#EC4F4E;
    --blush:#FCEDEE;
    --pink:#F8D3D4;
    --ink:#1c1c1c;
    --board:#f5f5f6;
  }
  *{box-sizing:border-box;margin:0;padding:0}
  html,body{width:1200px;height:1162px;overflow:hidden;background:var(--board);font-family:"Lato",sans-serif;color:var(--ink)}
  .board{position:relative;width:1200px;height:1162px}
  .slide{position:absolute;width:542px;height:305px;background:#fff;overflow:hidden;box-shadow:0 1px 4px rgba(0,0,0,.08)}
  .s1{left:42px;top:64px}.s2{left:620px;top:64px}
  .s3{left:42px;top:420px}.s4{left:620px;top:420px}
  .s5{left:42px;top:769px}.s6{left:620px;top:769px}
  .corner-tab{position:absolute;right:0;top:0;width:80px;height:70px}
  .corner-lines{position:absolute;left:0;bottom:0;width:48px;height:46px}
  .brand-mark{position:absolute;left:14px;top:18px;display:flex;align-items:center;gap:6px}
  .brand-dot{width:24px;height:24px;border-radius:50%;background:var(--bright)}
  .brand-name{font-weight:900;font-size:15px;color:var(--navy)}
  .page-no{position:absolute;right:13px;bottom:9px;display:flex;align-items:center;gap:6px;font-size:6px;color:#333}
  .page-no i{display:block;width:13px;height:13px;background:var(--bright);border-radius:3px 0 0 3px;margin-right:-13px}
  .heading{color:var(--navy);font-weight:700}
  .photo{position:absolute}
  /* slide 1 */
  .s1 .hero{left:181px;top:0;width:361px;height:305px;background:linear-gradient(135deg,#2d5fa8,#1b4d9a 55%,#123d80)}
  .s1 .brand-mark{left:28px;top:28px}
  .s1 .brand-dot{width:34px;height:34px}
  .s1 .brand-name{font-size:20px}
  .title-card{position:absolute;left:28px;top:107px;width:390px;height:138px;background:#fff;padding:27px 22px 0 23px;box-shadow:0 2px 8px rgba(0,0,0,.12)}
  .title-card h1{font-size:16.5px;line-height:21px;color:var(--navy);font-weight:700}
  .title-card p{font-size:11px;line-height:20px;margin-top:3px}
  /* slide 2 */
  .s2 h2{position:absolute;left:0;right:0;top:32px;text-align:center;font-size:16px}
  .member{position:absolute;width:90px;height:130px}
  .member .face{position:absolute;left:17px;top:52px;width:56px;height:56px;border-radius:50%;background:linear-gradient(160deg,#d9c2b0,#6b5144)}
  .member .tag{position:absolute;left:14px;top:0;width:62px;height:62px;transform:rotate(45deg);border-radius:8px;background:linear-gradient(135deg,var(--bright),var(--navy))}
  .member .label{position:absolute;left:0;top:18px;width:90px;text-align:center;color:#fff;font-size:5.2px;line-height:8.5px}
  /* slide 3 & 5 */
  .s3 .team-photo,.s5 .meeting-photo{width:165px;height:225px;border-right:4px solid var(--bright)}
  .s3 .team-photo{left:66px;top:47px;background:linear-gradient(160deg,#8a8c8e,#c8c2bb 50%,#6c6a68)}
  .s5 .meeting-photo{left:292px;top:42px;background:linear-gradient(180deg,#8ea7c9,#c9d4e0 45%,#6c5a4a)}
  .s3 h2{position:absolute;left:260px;top:42px;font-size:16px}
  .points{position:absolute;list-style:none}
  .points li{position:absolute;left:0;padding-left:17px;white-space:nowrap}
  .points li::before{content:"";position:absolute;left:0;top:0;width:6px;height:27px;border-radius:3px;background:var(--bright)}
  .s3 .points{left:260px;top:0}
  .s3 .points b{display:block;font-weight:400;font-size:9.5px;color:var(--navy);line-height:13px}
  .s3 .points span{display:block;font-size:7px;line-height:9.5px}
  /* slide 4 */
  .process-photo{left:122px;top:88px;width:297px;height:297px;border-radius:50%;background:linear-gradient(120deg,#6e5a4c,#d8dadc 45%,#f1f2f2)}
  .process-band{position:absolute;left:67px;top:77px;width:397px;height:103px;background:var(--bright);border-radius:4px;color:#fff}
  .process-band svg{position:absolute;left:99px;top:33px}
  .process-band .rule{position:absolute;left:151px;top:31px;width:1px;height:43px;background:#fff}
  .process-band h2{position:absolute;left:166px;top:29px;font-size:22px;font-weight:900}
  .process-band p{position:absolute;left:166px;top:58px;font-size:13px}
  /* slide 5 */
  .s5 h2{position:absolute;left:66px;top:66px;font-size:16px;line-height:21px}
  .s5 .points{left:66px;top:0}
  .s5 .points li{font-size:9.5px;color:var(--navy);line-height:14px}
  .s5 .points li::before{top:1px}
  /* slide 6 */
  .s6 h2{position:absolute;left:0;right:0;top:47px;text-align:center;font-size:16px}
  .flow{position:absolute;left:0;top:0}
  .step{position:absolute;width:62px;height:81px;background:var(--bright);border-radius:3px;color:#fff;font-size:7px;font-weight:700;line-height:9.5px;text-align:center;display:flex;flex-direction:column;align-items:center;justify-content:center;gap:5px;padding:0 3px}
</style>
</head>
<body>
<main class="board">

  <!-- Slide 1: cover -->
  <section class="slide s1">
    <div class="photo hero" role="img" aria-label="Smiling professional woman in an office, tinted blue"></div>
    <div class="brand-mark"><span class="brand-dot"></span><span class="brand-name">Loomline</span></div>
    <div class="title-card">
      <h1>Harwick State Public Institutions of Higher Education</h1>
      <p>Request for Proposal Furnish and Deliver Instructional Design and Media Production 1JNM2303</p>
    </div>
    <svg class="corner-lines" viewBox="0 0 48 46" fill="none" stroke="#d62a2a" stroke-width="1"><path d="M0 3 H30 Q44 3 44 17 V46"/><path d="M0 9 H26 Q38 9 38 21 V46"/></svg>
  </section>

  <!-- Slide 2: team -->
  <section class="slide s2">
    <div class="brand-mark"><span class="brand-dot"></span></div>
    <svg class="corner-tab" viewBox="0 0 80 70"><path d="M4 0 H80 V48 L48 64 Q38 69 34 59 Z" fill="var(--bright)"/></svg>
    <h2 class="heading">Our Team</h2>
    <div class="member" style="left:80px;top:78px"><div class="face" role="img" aria-label="Portrait of Daniel Porter"></div><div class="tag"></div><p class="label">Daniel Porter, PhD<br>COO</p></div>
    <div class="member" style="left:227px;top:78px"><div class="face" role="img" aria-label="Portrait of Renata Vale"></div><div class="tag"></div><p class="label">Renata Vale, MA<br>CEO</p></div>
    <div class="member" style="left:375px;top:78px"><div class="face" role="img" aria-label="Portrait of Tessa Morrow"></div><div class="tag"></div><p class="label">Tessa Morrow, CPACC<br>Vice President</p></div>
    <div class="member" style="left:153px;top:165px"><div class="face" role="img" aria-label="Portrait of Ingrid Hale"></div><div class="tag"></div><p class="label" style="top:16px">Ingrid Hale, MA<br>Research &amp; Development<br>Project Director</p></div>
    <div class="member" style="left:300px;top:157px"><div class="face" role="img" aria-label="Portrait of Miriam Castell"></div><div class="tag"></div><p class="label" style="top:16px">Miriam Castell, MA<br>Senior Manager of<br>Instructional Design</p></div>
    <svg class="corner-lines" viewBox="0 0 48 46" fill="none" stroke="#d62a2a" stroke-width="1"><path d="M0 3 H30 Q44 3 44 17 V46"/><path d="M0 9 H26 Q38 9 38 21 V46"/></svg>
    <div class="page-no">Page 2 <i></i></div>
  </section>

  <!-- Slide 3: about -->
  <section class="slide s3">
    <div class="brand-mark"><span class="brand-dot"></span></div>
    <svg class="corner-tab" viewBox="0 0 80 70"><path d="M4 0 H80 V48 L48 64 Q38 69 34 59 Z" fill="var(--bright)"/></svg>
    <div class="photo team-photo" role="img" aria-label="Young professional woman holding a laptop with colleagues behind"></div>
    <h2 class="heading">About Us</h2>
    <ul class="points">
      <li style="top:88px"><b>Woman/Minority Business</b><span>Certified Harwick State WMBE Woman/Minority<br>Business Enterprise</span></li>
      <li style="top:134px"><b>17 Years of Experience</b><span>In Business since 2006</span></li>
      <li style="top:168px"><b>Primary Focus</b><span>We are dedicated to creating top-notch<br>educational experiences through collaboration<br>with faculty and subject matter experts.</span></li>
      <li style="top:226px"><b>Principles</b><span>Communication, attention, and passion</span></li>
    </ul>
    <svg class="corner-lines" viewBox="0 0 48 46" fill="none" stroke="#d62a2a" stroke-width="1"><path d="M0 3 H30 Q44 3 44 17 V46"/><path d="M0 9 H26 Q38 9 38 21 V46"/></svg>
    <div class="page-no">Page 3 <i></i></div>
  </section>

  <!-- Slide 4: process divider -->
  <section class="slide s4">
    <div class="brand-mark"><span class="brand-dot"></span></div>
    <svg class="corner-tab" viewBox="0 0 80 70"><path d="M4 0 H80 V48 L48 64 Q38 69 34 59 Z" fill="var(--bright)"/></svg>
    <div class="photo process-photo" role="img" aria-label="Woman writing notes at a bright office desk"></div>
    <div class="process-band">
      <svg width="36" height="36" viewBox="0 0 36 36" fill="none" stroke="#fff" stroke-width="1.4"><circle cx="6" cy="6" r="4"/><rect x="12" y="3" width="22" height="7" rx="3.5"/><rect x="2" y="14" width="22" height="7" rx="3.5"/><rect x="2" y="25" width="22" height="7" rx="3.5"/><circle cx="30" cy="28" r="5"/><path d="M28 30 L32 26"/></svg>
      <span class="rule"></span>
      <h2>Process</h2>
      <p>Overview of Our Process</p>
    </div>
    <svg class="corner-lines" viewBox="0 0 48 46" fill="none" stroke="#d62a2a" stroke-width="1"><path d="M0 3 H30 Q44 3 44 17 V46"/><path d="M0 9 H26 Q38 9 38 21 V46"/></svg>
    <div class="page-no">Page 4 <i></i></div>
  </section>

  <!-- Slide 5: philosophy -->
  <section class="slide s5">
    <div class="brand-mark"><span class="brand-dot"></span></div>
    <svg class="corner-tab" viewBox="0 0 80 70"><path d="M4 0 H80 V48 L48 64 Q38 69 34 59 Z" fill="var(--bright)"/></svg>
    <h2 class="heading">Our Process<br>Philosophy</h2>
    <ul class="points">
      <li style="top:129px">Inspire Faculty</li>
      <li style="top:172px">Deliver Powerful and Effective Course Designs</li>
      <li style="top:215px">Equip Faculty with Cutting-Edge Concepts,<br>Tools, Research, and Best Practices</li>
    </ul>
    <div class="photo meeting-photo" role="img" aria-label="Team meeting in a glass-walled conference room"></div>
    <svg class="corner-lines" viewBox="0 0 48 46" fill="none" stroke="#d62a2a" stroke-width="1"><path d="M0 3 H30 Q44 3 44 17 V46"/><path d="M0 9 H26 Q38 9 38 21 V46"/></svg>
    <div class="page-no">Page 5 <i></i></div>
  </section>

  <!-- Slide 6: process overview -->
  <section class="slide s6">
    <div class="brand-mark"><span class="brand-dot"></span></div>
    <svg class="corner-tab" viewBox="0 0 80 70"><path d="M4 0 H80 V48 L48 64 Q38 69 34 59 Z" fill="var(--bright)"/></svg>
    <h2 class="heading">Process Overview</h2>
    <svg class="flow" width="542" height="305" viewBox="0 0 542 305">
      <g fill="var(--blush)"><circle cx="111" cy="134" r="58"/><circle cx="220" cy="197" r="58"/><circle cx="323" cy="134" r="58"/><circle cx="432" cy="199" r="58"/></g>
      <polyline points="0,190 111,134 220,197 323,134 432,199 542,160" fill="none" stroke="#d62a2a" stroke-width="1"/>
    </svg>
    <div class="step" style="left:80px;top:93px">
      <svg width="22" height="22" viewBox="0 0 22 22" fill="none" stroke="#fff" stroke-width="1.2"><path d="M11 2 L17 4 V9 Q17 14 11 16 Q5 14 5 9 V4 Z"/><path d="M8 9 L10.5 11.5 L14 7"/><path d="M2 18 Q8 16 12 19 L20 17"/></svg>
      <span>Course Quality Standards And Accessibility</span></div>
    <div class="step" style="left:189px;top:156px">
      <svg width="24" height="24" viewBox="0 0 24 24" fill="none" stroke="#fff" stroke-width="1.2"><rect x="3" y="3" width="8" height="8"/><rect x="13" y="3" width="8" height="8"/><rect x="3" y="13" width="8" height="8"/><rect x="13" y="13" width="8" height="8"/></svg>
      <span>Collaborative Approach</span></div>
    <div class="step" style="left:292px;top:93px">
      <svg width="22" height="22" viewBox="0 0 22 22" fill="none" stroke="#fff" stroke-width="1.2"><rect x="2" y="2" width="18" height="18" rx="1"/><path d="M5 6 H9 M5 10 H9 M12 12 H18 V18 H12 Z M15 12 V18 M12 15 H18"/></svg>
      <span>Robust Use Of Project Management Tools</span></div>
    <div class="step" style="left:401px;top:158px">
      <svg width="24" height="22" viewBox="0 0 24 22" fill="none" stroke="#fff" stroke-width="1.2"><circle cx="9" cy="13" r="6"/><circle cx="9" cy="13" r="2"/><circle cx="18" cy="6" r="4"/><circle cx="18" cy="6" r="1.3"/></svg>
      <span>10 Week Engagement Model</span></div>
    <svg class="corner-lines" viewBox="0 0 48 46" fill="none" stroke="#d62a2a" stroke-width="1"><path d="M0 3 H30 Q44 3 44 17 V46"/><path d="M0 9 H26 Q38 9 38 21 V46"/></svg>
    <div class="page-no">Page 6 <i></i></div>
  </section>

</main>
</body>
</html>
```